Ward Compass Business Card Design*

We need a business card design for our company Ward Compass. Our company is specialized in providing online consulting services regarding medical institutions, hospitals and doctors. We work with patients worldwide looking to choose between healthcare providers. We have a website you may use as a reference, where we list doctors and clinics worldwide. So we target Medical providers as well as patients worldwide.
Target Market(s)
Medical Providers and patients around the world
Industry/Entity Type
Medical
Contact Information for Business Card
Salwa Kettani
CEO
+90 612 348 2175
info@wardcompass.example
www.wardcompass.example
14 Annakhil 7 H.R.B. Rabat, Morocco
Requirements
Must have
- Company logo/name on one full side, personal info and smaller logo and company name on the other side.
Nice to have
- Smart and elegant design

```html
<!DOCTYPE html>
<html lang="en">
<head>
<meta charset="utf-8">
<title>Ward Compass — Business Card</title>
<link rel="stylesheet" href="https://fonts.googleapis.com/css2?family=Montserrat:wght@400;600;700&family=Lato:wght@400;700&display=swap">
<style>
  :root {
    --backdrop: #1c1c1e;
    --card-white: #ffffff;
    --blue-light: #35a6db;
    --blue-deep: #2f6fb8;
    --blue-ink: #2b63ad;
    --accent-sky: #3ba0dc;
    --text-dark: #2a2a2a;
    --divider: #e4e8ee;
  }
  * { box-sizing: border-box; margin: 0; padding: 0; }
  html, body {
    width: 1200px;
    height: 900px;
    overflow: hidden;
    background: var(--backdrop);
  }
  .stage {
    position: relative;
    width: 1200px;
    height: 900px;
  }
  .card {
    position: absolute;
    left: 290px;
    width: 620px;
    height: 354px;
    border-radius: 2px;
    box-shadow: 0 14px 34px rgba(0,0,0,.45);
    overflow: hidden;
  }
  /* Front side */
  .card--front {
    top: 70px;
    background: linear-gradient(160deg, var(--blue-light) 0%, var(--blue-deep) 100%);
    color: var(--card-white);
  }
  .front-brand {
    position: absolute;
    top: 128px;
    left: 0;
    right: 0;
    display: flex;
    align-items: center;
    justify-content: center;
    gap: 16px;
  }
  .front-brand__dot {
    width: 46px;
    height: 46px;
    border-radius: 50%;
    background: var(--card-white);
  }
  .front-brand__name {
    font-family: "Montserrat", sans-serif;
    font-weight: 600;
    font-size: 34px;
    letter-spacing: 1px;
    color: var(--card-white);
  }
  .front-web {
    position: absolute;
    bottom: 34px;
    left: 0;
    right: 0;
    text-align: center;
    font-family: "Lato", sans-serif;
    font-size: 15px;
    letter-spacing: 1.5px;
    color: var(--card-white);
  }
  /* Back side */
  .card--back {
    top: 472px;
    background: var(--card-white);
    display: flex;
  }
  .back-brand {
    flex: 0 0 350px;
    display: flex;
    align-items: center;
    justify-content: center;
    gap: 12px;
  }
  .back-brand__dot {
    width: 38px;
    height: 38px;
    border-radius: 50%;
    background: var(--blue-ink);
  }
  .back-brand__name {
    font-family: "Montserrat", sans-serif;
    font-weight: 600;
    font-size: 24px;
    letter-spacing: .5px;
    text-transform: uppercase;
    color: var(--blue-ink);
  }
  .back-divider {
    width: 1px;
    margin: 40px 0;
    background: var(--divider);
  }
  .contact {
    flex: 1;
    padding: 58px 0 0 30px;
    font-family: "Lato", sans-serif;
  }
  .contact__name {
    font-family: "Montserrat", sans-serif;
    font-size: 19px;
    text-transform: uppercase;
    line-height: 1.1;
  }
  .contact__first { font-weight: 700; color: var(--blue-ink); }
  .contact__last { font-weight: 400; color: var(--accent-sky); }
  .contact__role {
    font-size: 14px;
    color: var(--text-dark);
    margin-top: 3px;
    margin-bottom: 22px;
  }
  .contact__list { list-style: none; }
  .contact__item {
    display: flex;
    align-items: center;
    gap: 8px;
    font-size: 14.5px;
    color: var(--text-dark);
    line-height: 22px;
  }
  .contact__icon { width: 14px; height: 14px; flex: none; }
</style>
</head>
<body>
<main class="stage">
  <section class="card card--front" aria-label="Card front">
    <div class="front-brand">
      <span class="front-brand__dot"></span>
      <span class="front-brand__name">Ward Compass</span>
    </div>
    <p class="front-web">www.wardcompass.example</p>
  </section>

  <section class="card card--back" aria-label="Card back">
    <div class="back-brand">
      <span class="back-brand__dot"></span>
      <span class="back-brand__name">Ward Compass</span>
    </div>
    <div class="back-divider"></div>
    <div class="contact">
      <p class="contact__name"><span class="contact__first">Salwa</span> <span class="contact__last">Kettani</span></p>
      <p class="contact__role">CEO</p>
      <ul class="contact__list">
        <li class="contact__item">
          <svg class="contact__icon" viewBox="0 0 16 16" aria-hidden="true"><path fill="#3ba0dc" d="M3.6 1.5l2.3 2.6-1.3 1.7c.9 2 2.6 3.7 4.6 4.6l1.7-1.3 2.6 2.3-1.2 2.3C7 13.6 2.4 9 1.3 3.7z"/></svg>
          +90 612 348 2175
        </li>
        <li class="contact__item">
          <svg class="contact__icon" viewBox="0 0 16 16" aria-hidden="true"><rect x="1" y="3" width="14" height="10" rx="1" fill="#3ba0dc"/><path d="M1.5 3.8L8 9l6.5-5.2" stroke="#fff" stroke-width="1.3" fill="none"/></svg>
          info@wardcompass.example
        </li>
        <li class="contact__item">
          <svg class="contact__icon" viewBox="0 0 16 16" aria-hidden="true"><circle cx="8" cy="8" r="7" fill="#3ba0dc"/><path d="M1.5 8h13M8 1.2c2.4 2.2 2.4 11.4 0 13.6M8 1.2c-2.4 2.2-2.4 11.4 0 13.6" stroke="#fff" stroke-width="1" fill="none"/></svg>
          www.wardcompass.example
        </li>
      </ul>
    </div>
  </section>
</main>
</body>
</html>
```